Create an awesome website for a medical clinic

This is a new website for a doctor's office. The site should be clean and modern, easy to navigate.

This is a wellness clinic, we want to help our clients have a healthy, active lifestyle. It should be friendly and inviting, and easy for them to call or schedule an appointment.

The site should be responsive and designed using the attached Bootstrap 3 PSD.

We will provide stock photos, until then please use stock photos from:

pixelharbor.com or
framequarry.com (preferred)

Some example sites of clean and modern designs that we like:

https://tulsaspinecare.com/
http://reachpastjoints.com/
http://turninghealthier.com/

Also attached is a temporary logo you can use.

Reason: Thank you everyone for your great designs - we need a little more time so I'm extending the project.

Need extra days to review

Also, the colors in the new logo I just linked to are the final colors of the logo, so feel free to use any complimentary colors to it.

Hi everyone, The boss wants to change the layout of the site a little bit - here's the revised layout: https://www.filecrate.com/s/k9rt31vx2qp84zn/notes%2011_29_2017.pdf?dl=0 And the graphic assets you can use are here: https://www.filecrate.com/s/k9rt31vx2qp84zn/notes%2011_29_2017.pdf?dl=0 Feel free to change the background color of the "topbar", and change the icons of the "why people trust us" if you want, these are just temporary placeholders. Thanks for your patience and hard work!

Target Market(s)

People seeking medical treatment (wellness clinic)

Industry/Entity Type

Doctor

Number of Pages Required

1 page

Font styles to use
Sans Serif

Colors
0592cd
33a6d7
abd037
9bcb3c

Requirements
Must have
• The home page should have: a strong hero image/slideshow, clinic phone number should be prominent and at the top of the page (in the nav), a "what to expect" section (this is like a FAQs section - see attachment), and a strong call to action (a button to call or schedule an appointment).
• The what to expect section is useful so that prospective clients can determine if we're a good fit for them or not. It's a basic, first-step pre-qualification block of information.
• Social media icons which links to our social media profiles should be included.
Nice to have
• - Link to 3 most recent blog entries
• - Testimonials
• - How a multilevel nav menu looks.

```html
<!DOCTYPE html>
<html lang="en">
<head>
<meta charset="utf-8">
<title>Larkmere Clinic</title>
<link href="https://fonts.googleapis.com/css2?family=Montserrat:wght@600;700;800&family=Open+Sans:ital,wght@0,400;0,600;0,700;1,400&display=swap" rel="stylesheet">
<style>
:root{
  --blue:#0592cd;
  --blue-soft:#33a6d7;
  --green:#9bcb3c;
  --green-soft:#abd037;
  --ink:#222;
  --text:#555;
  --muted:#888;
  --line:#ddd;
  --grey-head:#6f6f6f;
  --footer:#2b2b2b;
  --white:#fff;
}
*{margin:0;padding:0;box-sizing:border-box}
html,body{width:1200px;height:3333px;overflow:hidden}
body{font-family:"Open Sans",Arial,sans-serif;color:var(--text);background:var(--white);position:relative}
.h{font-family:"Montserrat",Arial,sans-serif;font-weight:700;color:var(--ink);text-transform:uppercase}
.btn-ghost{position:absolute;border:2px solid var(--white);border-radius:30px;color:var(--white);font:700 15px "Montserrat",sans-serif;text-transform:uppercase;display:flex;align-items:center;justify-content:center;letter-spacing:.3px}

/* header */
.topline{position:absolute;top:0;left:0;width:1200px;height:5px;background:var(--blue-soft)}
.brand{position:absolute;left:98px;top:30px;display:flex;align-items:center;gap:12px}
.brand-mark{width:22px;height:22px;border-radius:50%;background:var(--green);flex:none}
.brand-name{font:700 30px/1 "Montserrat",sans-serif;color:var(--ink);letter-spacing:.5px}
.call{position:absolute;left:850px;top:20px;display:flex;align-items:center;font:700 18px "Montserrat",sans-serif;color:var(--ink)}
.call span{color:var(--blue);font-weight:600;margin-left:6px}
.call svg{margin-right:12px}
.nav{position:absolute;top:72px;left:404px;display:flex;font:600 15px "Montserrat",sans-serif;text-transform:uppercase;color:var(--ink)}
.nav a{margin-right:34px;color:inherit;text-decoration:none}
.nav a.active{color:var(--green)}

/* hero */
.hero{position:absolute;top:108px;left:0;width:1200px;height:444px;background:linear-gradient(90deg,#8a7a52 0%,#b59a61 35%,#6c8c9c 60%,#aab7b4 100%)}
.hero-title{position:absolute;left:96px;top:102px;font:800 58px/1.2 "Montserrat",sans-serif;color:var(--white);text-transform:uppercase;letter-spacing:1px}
.dots{position:absolute;display:flex;gap:7px}
.dots i{width:12px;height:12px;border-radius:50%;border:2px solid var(--white);display:block}
.dots i.on{background:var(--white)}

/* welcome */
.welcome-title{position:absolute;left:98px;top:640px;font-size:36px}
.welcome-copy{position:absolute;left:98px;top:700px;width:450px;font-size:14px;line-height:28px}
.welcome-copy p{margin-bottom:28px}
.btn-outline{position:absolute;border:2px solid var(--line);border-radius:30px;color:var(--green);font:700 14px "Montserrat",sans-serif;text-transform:uppercase;display:flex;align-items:center;justify-content:center}
.welcome-frame{position:absolute;left:605px;top:625px;width:505px;height:335px;border:2px solid var(--blue-soft);padding:10px}
.welcome-photo{width:100%;height:100%;background:linear-gradient(120deg,#e9eef2,#c8d6e0 50%,#f1f3f4)}

/* help */
.help{position:absolute;top:1033px;left:0;width:1200px;height:358px;background:linear-gradient(90deg,#8ec43d,#9bcb3c 60%,#a6cf55)}
.help-title{position:absolute;width:1200px;top:78px;text-align:center;color:var(--white);font-size:36px}
.help-copy{position:absolute;left:200px;width:800px;top:132px;text-align:center;color:var(--white);font-size:14px;line-height:28px}

/* blog */
.section-title{position:absolute;width:1200px;text-align:center;font-size:36px}
.post{position:absolute;top:1547px;width:315px}
.post-img{height:184px}
.post-title{font:700 19px "Montserrat",sans-serif;color:var(--ink);margin-top:34px}
.post-meta{font-size:13px;color:var(--text);margin-top:12px;display:flex;align-items:center;gap:6px}
.post-text{font-size:14px;line-height:24px;margin-top:14px}
.read{font:700 13px "Montserrat",sans-serif;color:var(--green);text-transform:uppercase;margin-top:12px}

/* testimonials */
.testi{position:absolute;top:1982px;left:0;width:1200px;height:394px;background:linear-gradient(90deg,#2f9fd4,#44ade0 50%,#3aa2d5)}
.testi-title{position:absolute;width:1200px;top:68px;text-align:center;color:var(--white);font-size:34px}
.quote{position:absolute;top:148px;width:345px}
.avatar{position:absolute;left:0;top:0;width:74px;height:74px;border-radius:50%;background:#d9e3e8;border:3px solid var(--white)}
.quote-text{margin-left:98px;font-style:italic;font-size:12.5px;line-height:24px;color:var(--white)}
.quote-text b{font-size:20px;font-style:normal;margin-right:6px}
.quote-name{margin-left:98px;margin-top:14px;font:700 11px "Montserrat",sans-serif;color:var(--white);text-transform:uppercase}
.quote-role{margin-left:98px;font-style:italic;font-size:10.5px;color:var(--white);margin-top:4px}
.stars{margin-left:88px;margin-top:20px;display:flex}
.arrow-btn{position:absolute;top:2185px;width:32px;height:32px;border-radius:50%;border:2px solid rgba(255,255,255,.8);display:flex;align-items:center;justify-content:center}

/* expect */
.card{position:absolute;top:2525px;width:315px;height:151px;border:1px solid var(--line)}
.card-head{height:33px;background:var(--grey-head);color:var(--white);font:700 16px "Montserrat",sans-serif;padding:7px 12px}
.card-head.green{background:var(--green)}
.card-body{padding:18px 20px;font-size:14px;line-height:25px}

/* footer */
.footer{position:absolute;top:2793px;left:0;width:1200px;height:540px;background:linear-gradient(180deg,#2d2d2d,#242424)}
.footer .to-top{position:absolute;left:560px;top:18px;width:80px;text-align:center;color:var(--white);font:700 13px "Montserrat",sans-serif}
.f-title{position:absolute;top:140px;color:var(--white);font-size:21px}
.field{position:absolute;background:var(--white);font-size:11px;color:#666;padding:0 12px;display:flex;align-items:center}
.field.msg{align-items:flex-start;padding-top:10px}
.submit{position:absolute;left:637px;top:390px;width:90px;height:34px;border-radius:20px;background:var(--green);color:var(--white);font:700 14px "Montserrat",sans-serif;display:flex;align-items:center;justify-content:center}
.info-row{position:absolute;left:780px;display:flex;align-items:center;gap:24px;color:var(--white);font-size:13px}
.info-ico{width:34px;height:34px;border:2px solid #777;border-radius:50%;display:flex;align-items:center;justify-content:center}
.socials{position:absolute;left:780px;top:368px;display:flex;gap:12px}
.socials i{width:30px;height:30px;border-radius:50%;display:block}
.f-rule{position:absolute;left:98px;top:463px;width:1004px;height:1px;background:#444}
.copy{position:absolute;top:500px;width:1200px;text-align:center;font-size:12px;color:#ccc}
</style>
</head>
<body>

<header>
  <div class="topline"></div>
  <div class="brand">
    <div class="brand-mark"></div>
    <div class="brand-name">LARKMERE CLINIC</div>
  </div>
  <div class="call">
    <svg width="26" height="26" viewBox="0 0 26 26"><circle cx="13" cy="13" r="12" fill="none" stroke="#9bcb3c" stroke-width="1.5"/><path d="M9 7.5c.6-.6 1.5-.5 2 .2l1 1.6c.4.6.2 1.3-.3 1.7l-.7.5c.6 1.5 1.7 2.7 3.2 3.4l.6-.7c.4-.5 1.2-.6 1.7-.2l1.6 1c.7.5.8 1.4.2 2l-.8.8c-3.8 1-10-5.2-9-9z" fill="#9bcb3c"/></svg>
    CALL : <span>1 800 555 0142</span>
  </div>
  <nav class="nav">
    <a class="active">Home</a><a>About</a><a>Services</a><a>Testimonials</a><a>Resources</a><a>Contact Us</a>
    <svg width="16" height="16" viewBox="0 0 16 16"><circle cx="6.5" cy="6.5" r="4.5" fill="none" stroke="#222" stroke-width="2.2"/><path d="M10 10l4 4" stroke="#222" stroke-width="2.5"/></svg>
  </nav>
</header>

<section class="hero" role="img" aria-label="Smiling woman jogging along a sunny lakeside path">
  <h1 class="hero-title">Healthy,<br>Active Lifestyle</h1>
  <div class="btn-ghost" style="left:98px;top:274px;width:268px;height:52px">Schedule an Appointment</div>
  <div class="dots" style="left:567px;top:382px"><i class="on"></i><i></i><i></i><i></i></div>
</section>

<section class="welcome">
  <h2 class="h welcome-title">Welcome to Larkmere</h2>
  <div class="welcome-copy">
    <p>Nam libero tempore, cum soluta nobis est eligendi optio cumque nih il impedit quo minus id quod maxime placeat.</p>
    <p>Fere possimus, omnis voluptas assumenda est, omnis dolor repellen dus. Temporibus autem quibusdam et aut officiis debitis aut rerum necessitatibus saepe eveniet ut et voluptates.</p>
  </div>
  <div class="btn-outline" style="left:98px;top:885px;width:142px;height:46px">Read More</div>
  <div class="welcome-frame"><div class="welcome-photo" role="img" aria-label="Nurse and doctor greeting an older patient in a bright clinic room"></div></div>
</section>

<section class="help">
  <h2 class="h help-title">How can we help you</h2>
  <p class="help-copy">Nam libero tempore, cum soluta nobis est eligendi optio cumque nihil impedit quo minus id quod maxime placeat facere possimus, omnis voluptas assumenda est, omnis dolor repellendnporibus autem quibusdam et aut officiis debitis aut rerum necessitatibus saepe eveniet ut et voluptates repudiandae sint et moles.</p>
  <div class="btn-ghost" style="left:465px;top:235px;width:268px;height:52px">Schedule an Appointment</div>
</section>

<section class="blog">
  <h2 class="h section-title" style="top:1466px">Recent Blog</h2>
  <article class="post" style="left:98px">
    <div class="post-img" role="img" aria-label="Woman stretching her arms by the sea under a blue sky" style="background:linear-gradient(180deg,#6fb2e0,#d7e8f2 60%,#8a8f7d)"></div>
    <div class="post-title">Finibus Bonorumet Malorum</div>
    <div class="post-meta"><svg width="12" height="12" viewBox="0 0 12 12"><rect x="1" y="2" width="10" height="9" fill="none" stroke="#0592cd" stroke-width="1.5"/><path d="M1 5h10" stroke="#0592cd"/></svg>25/09/2017 &nbsp;|&nbsp; <svg width="12" height="12" viewBox="0 0 12 12"><circle cx="6" cy="4" r="2.6" fill="#0592cd"/><path d="M1 12c0-3 2.2-4.5 5-4.5s5 1.5 5 4.5z" fill="#0592cd"/></svg>John</div>
    <p class="post-text">At vero eos et accusamus et iusto odio dignissimodu cimus qui blanditiis praesentium.</p>
    <div class="read">Read More</div>
  </article>
  <article class="post" style="left:442px">
    <div class="post-img" role="img" aria-label="Nurse taking blood pressure of a senior woman" style="background:linear-gradient(120deg,#cfd6dc,#eef0f2 50%,#b9c4cc)"></div>
    <div class="post-title">Finibus Bonorumet Malorum</div>
    <div class="post-meta"><svg width="12" height="12" viewBox="0 0 12 12"><rect x="1" y="2" width="10" height="9" fill="none" stroke="#0592cd" stroke-width="1.5"/><path d="M1 5h10" stroke="#0592cd"/></svg>25/09/2017 &nbsp;|&nbsp; <svg width="12" height="12" viewBox="0 0 12 12"><circle cx="6" cy="4" r="2.6" fill="#0592cd"/><path d="M1 12c0-3 2.2-4.5 5-4.5s5 1.5 5 4.5z" fill="#0592cd"/></svg>John</div>
    <p class="post-text">At vero eos et accusamus et iusto odio dignissimodu cimus qui blanditiis praesentium.</p>
    <div class="read">Read More</div>
  </article>
  <article class="post" style="left:786px">
    <div class="post-img" role="img" aria-label="Senior couple walking hand in hand on a beach" style="background:linear-gradient(180deg,#7fb3dd,#b8d3e6 45%,#d8c49a)"></div>
    <div class="post-title">Finibus Bonorumet Malorum</div>
    <div class="post-meta"><svg width="12" height="12" viewBox="0 0 12 12"><rect x="1" y="2" width="10" height="9" fill="none" stroke="#0592cd" stroke-width="1.5"/><path d="M1 5h10" stroke="#0592cd"/></svg>25/09/2017 &nbsp;|&nbsp; <svg width="12" height="12" viewBox="0 0 12 12"><circle cx="6" cy="4" r="2.6" fill="#0592cd"/><path d="M1 12c0-3 2.2-4.5 5-4.5s5 1.5 5 4.5z" fill="#0592cd"/></svg>John</div>
    <p class="post-text">At vero eos et accusamus et iusto odio dignissimodu cimus qui blanditiis praesentium.</p>
    <div class="read">Read More</div>
  </article>
</section>

<section class="testi" role="img" aria-label="Blue tinted photo of a woman running in a park">
  <h2 class="h testi-title">Testimonials</h2>
  <div class="quote" style="left:98px">
    <div class="avatar" role="img" aria-label="Client portrait"></div>
    <p class="quote-text"><b>“</b>Friendly staff and clear advice helped me get back to running every single week.</p>
    <div class="quote-name">Marisa Hallett</div>
    <div class="quote-role">Marketing Consultant</div>
    <div class="stars"><svg width="100" height="18" viewBox="0 0 100 18"><g fill="#abd037"><path id="s" d="M9 1l2.4 5.2 5.6.6-4.2 3.8 1.2 5.6L9 13.4 4 16.2l1.2-5.6L1 6.8l5.6-.6z"/><use href="#s" x="20"/><use href="#s" x="40"/><use href="#s" x="60"/></g><use href="#s" x="80" fill="none" stroke="#abd037" stroke-width="1.3"/></svg></div>
  </div>
  <div class="quote" style="left:442px">
    <div class="avatar" role="img" aria-label="Client portrait"></div>
    <p class="quote-text"><b>“</b>The doctors listened carefully and built a plan that truly fit my busy life.</p>
    <div class="quote-name">Trent L. Oakley</div>
    <div class="quote-role">Urban Planning Fellow</div>
    <div class="stars"><svg width="100" height="18" viewBox="0 0 100 18"><g fill="#abd037"><use href="#s"/><use href="#s" x="20"/><use href="#s" x="40"/><use href="#s" x="60"/></g><use href="#s" x="80" fill="none" stroke="#abd037" stroke-width="1.3"/></svg></div>
  </div>
  <div class="quote" style="left:786px">
    <div class="avatar" role="img" aria-label="Client portrait"></div>
    <p class="quote-text"><b>“</b>Booking was easy, the visit was calm, and I left feeling cared for today.</p>
    <div class="quote-name">Celia Brandt</div>
    <div class="quote-role">Creative Strategist | Entrepreneur</div>
    <div class="stars"><svg width="100" height="18" viewBox="0 0 100 18"><g fill="#abd037"><use href="#s"/><use href="#s" x="20"/><use href="#s" x="40"/><use href="#s" x="60"/></g><use href="#s" x="80" fill="none" stroke="#abd037" stroke-width="1.3"/></svg></div>
  </div>
</section>
<div class="arrow-btn" style="left:30px"><svg width="10" height="12" viewBox="0 0 10 12"><path d="M7 1L2 6l5 5" fill="none" stroke="#fff" stroke-width="2"/></svg></div>
<div class="arrow-btn" style="left:1136px"><svg width="10" height="12" viewBox="0 0 10 12"><path d="M3 1l5 5-5 5" fill="none" stroke="#fff" stroke-width="2"/></svg></div>

<section class="expect">
  <h2 class="h section-title" style="top:2446px">What to Expect</h2>
  <div class="card" style="left:98px"><div class="card-head">Finibus Bonorumet Malorum?</div><p class="card-body">Nam libero tempore, cum soluta nobis essrt eligendi optio cumque nihil impedit quomin us id quod maxime placea.</p></div>
  <div class="card" style="left:442px"><div class="card-head green">Finibus Bonorumet Malorum?</div><p class="card-body">Nam libero tempore, cum soluta nobis essrt eligendi optio cumque nihil impedit quomin us id quod maxime placea.</p></div>
  <div class="card" style="left:786px"><div class="card-head">Finibus Bonorumet Malorum?</div><p class="card-body">Nam libero tempore, cum soluta nobis essrt eligendi optio cumque nihil impedit quomin us id quod maxime placea.</p></div>
  <div class="dots" style="left:578px;top:2706px"><i class="on" style="border-color:#888;background:#888"></i><i style="border-color:#888"></i><i style="border-color:#888"></i></div>
</section>

<footer class="footer" role="img" aria-label="Dark tinted photo of a doctor at work">
  <div class="to-top">
    <svg width="70" height="20" viewBox="0 0 70 20"><path d="M0 20L35 0l35 20z" fill="#3c3c3c"/></svg>
    <div style="margin-top:6px">TO TOP</div>
  </div>
  <h3 class="h f-title" style="left:96px">Contact Form</h3>
  <div class="field" style="left:98px;top:203px;width:310px;height:32px">Name :</div>
  <div class="field" style="left:416px;top:203px;width:311px;height:32px">Phone no :</div>
  <div class="field" style="left:98px;top:245px;width:629px;height:32px">Email :</div>
  <div class="field msg" style="left:98px;top:287px;width:629px;height:82px">Message :</div>
  <div class="submit">SUBMIT</div>

  <h3 class="h f-title" style="left:780px">Contact Information</h3>
  <div class="info-row" style="top:202px"><div class="info-ico"><svg width="12" height="16" viewBox="0 0 12 16"><path d="M6 0a6 6 0 0 1 6 6c0 4-6 10-6 10S0 10 0 6a6 6 0 0 1 6-6z" fill="#fff"/><circle cx="6" cy="6" r="2.2" fill="#2b2b2b"/></svg></div>412 Larkfield Road Easton MA 02375</div>
  <div class="info-row" style="top:254px"><div class="info-ico"><svg width="14" height="14" viewBox="0 0 14 14"><path d="M2 .8c.7-.7 1.7-.6 2.2.2l1.1 1.8c.4.6.2 1.4-.3 1.8l-.8.6c.7 1.6 1.9 2.9 3.5 3.7l.7-.8c.4-.5 1.3-.7 1.9-.2l1.8 1.1c.8.5.9 1.5.2 2.2l-.9.9C7.2 13.2.1 6.2 1.1 1.7z" fill="#fff"/></svg></div>1 800 555 0142</div>
  <div class="info-row" style="top:306px"><div class="info-ico"><svg width="14" height="10" viewBox="0 0 14 10"><rect width="14" height="10" fill="#fff"/><path d="M0 0l7 5.5L14 0" fill="none" stroke="#2b2b2b" stroke-width="1.3"/></svg></div>hello@larkmereclinic.com</div>
  <div class="socials"><i style="background:#3b5998"></i><i style="background:#1da1f2"></i><i style="background:#0077b5"></i><i style="background:#cb2027"></i></div>
  <div class="f-rule"></div>
  <p class="copy">Copyright © 2017, Larkmere Clinic. All rights reserved.</p>
</footer>

</body>
</html>
```